Commercial Swimming Pool - Design-Build Contractor Website Design

I need a new website that will feature our newly developed logo and trade name as well as provide a fully updated site experience. We are not a residential builder - we strictly design and install high-end commercial pools. I need the website to highlight our portfolio and communicate the various types of projects in which we specialize. I want the effect of the site to reflect the high-end nature of our services - projects like the 57th floor spa at the Phila Silver Willow, the aquatic therapy portion of the Phila Ravenhawks training facility, a 5om indoor competition pool for the prestigious Dallowmere Academy, the indoor water park at The Quenwick Lodge or the recent country club renovation projects we've completed in our region (to name a few examples).
Need extra days to review

```html
<!DOCTYPE html>
<html lang="en">
<head>
<meta charset="utf-8">
<title>Marlowe Aquatics — Commercial Pools</title>
<link href="https://fonts.googleapis.com/css2?family=Jost:wght@400;500;600;700&family=Poppins:ital,wght@0,400;0,500;0,600;0,700;1,400;1,600&display=swap" rel="stylesheet">
<style>
:root{
  --navy:#14214d;
  --deep:#1d3b83;
  --deep-2:#264c9c;
  --accent:#3aa6e0;
  --accent-soft:#55b9ea;
  --ink:#222;
  --mute:#f4f4f4;
  --white:#fff;
}
*{box-sizing:border-box;margin:0;padding:0}
html,body{width:1200px;height:5034px;overflow:hidden}
body{position:relative;background:var(--white);font-family:"Poppins",sans-serif;color:var(--ink)}
.abs{position:absolute}
.head-font{font-family:"Jost",sans-serif}

/* header */
.brand{left:130px;top:28px;display:flex;align-items:center;gap:10px}
.brand-mark{width:46px;height:46px;border-radius:50%;background:var(--deep)}
.brand-name{font-family:"Jost",sans-serif;font-weight:600;font-size:30px;color:var(--deep);letter-spacing:1px;line-height:1}
.call{left:615px;top:32px;font-family:"Jost",sans-serif;font-weight:600;font-size:19px;color:var(--navy);display:flex;align-items:center;gap:10px}
.call b{color:var(--accent);font-weight:500}
.phone-dot{width:24px;height:24px;border-radius:50%;background:var(--accent);display:flex;align-items:center;justify-content:center}
.btn{display:flex;align-items:center;gap:10px;border-radius:24px;background:var(--accent-soft);color:var(--white);font-weight:600;text-transform:uppercase}
.btn .arrow{width:28px;height:28px;border-radius:50%;background:var(--navy);display:flex;align-items:center;justify-content:center}
.quote-btn{left:908px;top:22px;width:164px;height:44px;padding:0 8px;font-size:11px}
.nav{left:475px;top:86px;display:flex;gap:0;font-size:12.5px;font-weight:500;color:var(--navy)}
.nav a{color:inherit;text-decoration:none;margin-right:38px}
.nav a.on{color:var(--accent)}

.hero-photo{left:0;top:130px;width:1200px;height:680px;background:linear-gradient(160deg,#4fc3ee 0%,#1f9ad8 45%,#6fd1f2 75%,#2a8fd0 100%)}
.hero-title{left:78px;top:305px;font-family:"Jost",sans-serif;font-weight:600;font-size:76px;line-height:.82;color:var(--navy);letter-spacing:2px}
.hero-tag{left:80px;top:455px;font-size:16px;color:var(--navy);letter-spacing:.5px}
.hero-btn{left:80px;top:500px;width:182px;height:44px;padding:0 8px;font-size:12px}

.welcome-title{left:160px;top:838px;font-family:"Jost",sans-serif;font-weight:600;font-size:44px;line-height:1.2;color:var(--white);letter-spacing:1px}
.welcome-title span{color:var(--accent)}
.welcome-text{left:160px;top:970px;width:480px;font-size:15px;line-height:21px;color:var(--white)}
.welcome-mark{left:705px;top:1010px;width:340px;text-align:center;font-family:"Jost",sans-serif;font-weight:700;font-size:54px;line-height:1.05;color:var(--white);letter-spacing:3px}

.section-title{width:1200px;left:0;text-align:center;font-family:"Jost",sans-serif;font-weight:600;color:var(--navy);letter-spacing:1px}
.section-title span{color:var(--accent)}
.services-title{top:1410px;font-size:38px;line-height:44px}
.services{left:115px;top:1535px;width:970px;display:flex}
.service{flex:1;height:190px;display:flex;flex-direction:column;align-items:center;border-right:2px solid #bbb}
.service:last-child{border-right:none}
.service svg{margin-top:12px}
.service p{margin-top:26px;font-size:19px;line-height:23px;text-align:center;color:var(--ink)}

.lead{width:1200px;left:0;text-align:center;font-size:18px;line-height:22px;color:var(--ink)}
.projects-title{top:1932px;font-size:44px}
.card{width:370px;height:315px;background:var(--white);box-shadow:0 2px 10px rgba(0,0,0,.08)}
.card .shot{height:214px}
.card p{padding:0 36px;margin-top:24px;text-align:center;font-size:16px;line-height:20px;font-weight:600;color:var(--navy)}

.testi-title{top:2968px;font-size:42px;color:var(--white)}
.avatar{left:208px;top:3038px;width:154px;height:154px;border-radius:50%;border:6px solid var(--white);background:linear-gradient(135deg,#c9d7e6,#7a8fa8)}
.quote-mark{left:205px;top:3085px;width:38px;height:38px;border-radius:50%;background:var(--navy);color:var(--white);font-size:22px;font-weight:700;text-align:center;line-height:44px}
.testi-text{left:405px;top:3092px;width:595px;font-style:italic;font-size:20px;line-height:24px;color:#eaf7ff}
.testi-name{left:413px;top:3230px;font-style:italic;font-weight:600;font-size:20px;color:var(--white)}

.gallery-title{top:3456px;font-size:44px}
.tile{background:linear-gradient(135deg,#3fb5e6,#1577bf)}
.more-btn{left:528px;top:4058px;width:144px;height:46px;justify-content:center;font-size:12px}

.contact-title{top:4400px;font-size:44px;color:var(--white)}
.contact-lead{top:4474px;font-size:14px;line-height:18px;color:#e6ecf8}
.field{border:1px solid #c7d1ea;border-radius:6px;color:#e6ecf8;font-size:12px;padding:10px 14px}
.info{display:flex;align-items:center;gap:16px;color:var(--white);font-size:14px;line-height:18px}
.info .dot{width:56px;height:56px;border-radius:50%;background:var(--accent-soft);display:flex;align-items:center;justify-content:center;flex:none}

.social{left:150px;top:4930px;width:183px;height:64px;border:1px solid #555;border-radius:6px;display:flex;align-items:center;justify-content:center;gap:14px}
.social i{width:20px;height:20px;border-radius:50%;background:var(--navy);display:block}
.foot-brand{left:470px;top:4945px}
.copy{left:795px;top:4943px;font-size:13px;line-height:19px;color:var(--navy)}
</style>
</head>
<body>

<!-- header -->
<div class="abs brand"><span class="brand-mark"></span><span class="brand-name">MARLOWE<br><span style="font-size:20px">AQUATICS</span></span></div>
<div class="abs call"><span class="phone-dot"><svg width="12" height="12" viewBox="0 0 24 24"><path fill="#fff" d="M6.6 10.8a15 15 0 0 0 6.6 6.6l2.2-2.2a1 1 0 0 1 1-.25 11.4 11.4 0 0 0 3.6.57 1 1 0 0 1 1 1V20a1 1 0 0 1-1 1A17 17 0 0 1 3 4a1 1 0 0 1 1-1h3.5a1 1 0 0 1 1 1c0 1.25.2 2.45.57 3.6a1 1 0 0 1-.25 1z"/></svg></span>CALL US: <b>555 010 2040</b></div>
<div class="abs btn quote-btn"><span class="arrow"><svg width="10" height="10" viewBox="0 0 10 10"><path d="M3 1l4 4-4 4" stroke="#fff" stroke-width="1.6" fill="none"/></svg></span>Get a quote</div>
<nav class="abs nav"><a class="on">HOME</a><a>ABOUT US</a><a>SERVICES</a><a>PROJECTS</a><a>GALLERY</a><a>CONTACT US</a></nav>

<!-- hero -->
<div class="abs hero-photo" role="img" aria-label="Photo of a child riding an inflatable ring through splashing pool water"></div>
<svg class="abs" style="left:0;top:600px" width="1200" height="720" viewBox="0 600 1200 720" role="img" aria-label="Dark blue tinted photo of pool lanes">
  <defs><linearGradient id="navyWash" x1="0" y1="0" x2="1" y2="1"><stop offset="0" stop-color="#24468f"/><stop offset="1" stop-color="#183473"/></linearGradient></defs>
  <path fill="url(#navyWash)" d="M0,690 C140,610 330,620 520,700 C690,770 900,790 1060,720 C1130,690 1170,660 1200,630 L1200,1235 C1000,1295 760,1310 520,1290 C320,1272 150,1245 0,1228 Z"/>
</svg>
<div class="abs hero-title">MARLOWE<br>AQUATICS</div>
<div class="abs hero-tag">DESIGN &nbsp;|&nbsp; CONSTRUCTION &nbsp;|&nbsp; EXCELLENCE</div>
<div class="abs btn hero-btn"><span class="arrow"><svg width="10" height="10" viewBox="0 0 10 10"><path d="M3 1l4 4-4 4" stroke="#fff" stroke-width="1.6" fill="none"/></svg></span>View projects</div>

<!-- welcome -->
<h1 class="abs welcome-title">WELCOME TO<br><span>MARLOWE AQUATICS</span></h1>
<p class="abs welcome-text">Lorem ipsum dolor sit amet, consectetur adipiscing elit, sed do eiusmod tempor incididunt ut labore et dolore magna aliqua. Quis ipsum suspendisse ultrices gravida. Risus commodo viverra maecenas accumsanorem ipsum dolor sit amet, consectetur adipiscing elit, sed do eiusmod tempor incididunt ut labore et dolore magna aliqua. Quis ipsum suspendisse ultrices gravida.</p>
<div class="abs welcome-mark">MARLOWE<br>AQUATICS</div>

<!-- services -->
<h2 class="abs section-title services-title">COMMERCIAL SWIMMING<br>POOL <span>SERVICES</span></h2>
<div class="abs services">
  <div class="service">
    <svg width="80" height="80" viewBox="0 0 80 80" fill="none" stroke="#1d3b83" stroke-width="3"><path d="M24 10v44M50 10v44M24 22h26M24 34h26M24 46h26"/><path d="M24 10a6 6 0 0 0-12 0M50 10a6 6 0 0 0-12 0" stroke="#3aa6e0"/><path d="M6 60q7-5 14 0t14 0 14 0 14 0 14 0M6 70q7-5 14 0t14 0 14 0 14 0 14 0"/></svg>
    <p>Swimming Pool<br>Design</p>
  </div>
  <div class="service">
    <svg width="80" height="80" viewBox="0 0 80 80" fill="none" stroke="#1d3b83" stroke-width="3"><path d="M14 8v26M10 8h8M14 34v30"/><path d="M30 10v24" stroke="#3aa6e0"/><circle cx="56" cy="20" r="9" stroke="#3aa6e0"/><path d="M22 72V56a18 18 0 0 1 36 0v16zM18 72h44"/></svg>
    <p>Swimming Pool<br>Construction</p>
  </div>
  <div class="service">
    <svg width="80" height="80" viewBox="0 0 80 80" fill="none" stroke="#1d3b83" stroke-width="3"><path d="M10 10h30M25 10v14M18 24h14v40H18z"/><path d="M46 40h24l-6 30H40z" stroke="#3aa6e0"/><path d="M50 42l-4 26M60 42l-4 26M44 55h24" stroke="#3aa6e0"/><path d="M60 12v12M54 18h12M8 40h6M11 37v6"/></svg>
    <p>Pool Tile Cleaning<br>Services</p>
  </div>
  <div class="service">
    <svg width="80" height="80" viewBox="0 0 80 80" fill="none" stroke="#1d3b83" stroke-width="3"><path d="M30 40l24-24M30 16l24 24" stroke="#3aa6e0"/><circle cx="56" cy="14" r="5" stroke="#3aa6e0"/><path d="M6 52h12v18H6zM18 54h16l14 6 14-8a4 4 0 0 1 4 6L46 70H18"/></svg>
    <p>Routine<br>Maintenance</p>
  </div>
</div>

<!-- projects -->
<svg class="abs" style="left:0;top:1860px" width="1200" height="690" viewBox="0 1860 1200 690"><path fill="#f4f4f4" d="M0,1945 C250,1870 600,1865 900,1878 C1050,1886 1150,1898 1200,1905 L1200,2545 L0,2545 Z"/></svg>
<h2 class="abs section-title projects-title">OUR <span>PROJECTS</span></h2>
<p class="abs lead" style="top:2002px">Lorem ipsum dolor sit amet, consectetur adipiscing elit, sed do eiusmod<br>tempor incididunt ut labore et dolore magna aliquasum suspen</p>
<article class="abs card" style="left:215px;top:2097px"><div class="shot" role="img" aria-label="Woman relaxing at the edge of a rooftop spa" style="background:linear-gradient(135deg,#8aa08a,#b9c7c4 50%,#5fb0cf)"></div><p>the 57th floor spa at the Phila Silver Willow</p></article>
<article class="abs card" style="left:615px;top:2097px"><div class="shot" role="img" aria-label="Swimmers with kickboards in an aquatic therapy pool" style="background:linear-gradient(135deg,#29a5e0,#1279c4)"></div><p>The aquatic therapy portion of the Phila Ravenhawks training facility.</p></article>
<article class="abs card" style="left:215px;top:2440px"><div class="shot" role="img" aria-label="Swimmers training in lanes of an indoor competition pool" style="background:linear-gradient(135deg,#5ec5ec,#1a88cf)"></div><p>a 5om indoor competition pool for the prestigious Dallowmere Academy</p></article>
<article class="abs card" style="left:615px;top:2440px"><div class="shot" role="img" aria-label="Indoor water park with slides and a rider on a float" style="background:linear-gradient(135deg,#2f7ec6,#56c0ec 60%,#9fe0f5)"></div><p>the indoor water park at The Quenwick Lodge or the recent country club renovation</p></article>

<!-- testimonials -->
<svg class="abs" style="left:0;top:2780px" width="1200" height="585" viewBox="0 2780 1200 585" role="img" aria-label="Rippling turquoise pool water">
  <defs><linearGradient id="waterWash" x1="0" y1="0" x2="1" y2="1"><stop offset="0" stop-color="#2fb4ea"/><stop offset=".5" stop-color="#1d9ddc"/><stop offset="1" stop-color="#48c4ef"/></linearGradient></defs>
  <path fill="url(#waterWash)" d="M0,2810 C200,2805 360,2905 600,2885 C850,2862 1000,2800 1200,2812 L1200,3362 L0,3362 Z"/>
</svg>
<h2 class="abs section-title testi-title">CLIENT TESTIMONIALS</h2>
<div class="abs avatar" role="img" aria-label="Portrait photo of the client"></div>
<div class="abs quote-mark">“</div>
<p class="abs testi-text">Lorem ipsum dolor sit amet, consectetur adipiscing elit, sed do eiusmod tempor incididunt ut labore et dolore magna aliqua. Quis ipsum suspendisse ultrices gravida. Risus commodo viverra maecenas accumsan lacus vel facilisis.</p>
<p class="abs testi-name">– Dana Whitfield, Harbor spa</p>

<!-- gallery -->
<h2 class="abs section-title gallery-title">OUR <span>GALLERY</span></h2>
<p class="abs lead" style="top:3524px">Lorem ipsum dolor sit amet, consectetur adipiscing elit, sed do eiusmod<br>tempor incididunt ut labore et dolore magna aliquais ipsum sus.</p>
<div class="abs tile" style="left:152px;top:3622px;width:284px;height:178px" role="img" aria-label="Swimmers with a yellow kickboard"></div>
<div class="abs tile" style="left:458px;top:3622px;width:284px;height:394px;background:linear-gradient(180deg,#7fcdf0,#35aee6 60%,#8ad8f5)" role="img" aria-label="Child jumping into a pool with a splash"></div>
<div class="abs tile" style="left:765px;top:3622px;width:284px;height:178px;background:linear-gradient(135deg,#1f8fd6,#0f5fa8)" role="img" aria-label="Lane rope in clear pool water"></div>
<div class="abs tile" style="left:152px;top:3822px;width:284px;height:194px;background:linear-gradient(180deg,#c7ced6,#8fa3b8 40%,#2b8fd6)" role="img" aria-label="Large indoor natatorium"></div>
<div class="abs tile" style="left:765px;top:3822px;width:284px;height:194px;background:linear-gradient(180deg,#c9a97e,#8fd0d8 55%,#4aaed6)" role="img" aria-label="Indoor hotel pool with ladders"></div>
<div class="abs btn more-btn">View more</div>

<!-- contact -->
<svg class="abs" style="left:0;top:4140px" width="1200" height="770" viewBox="0 4140 1200 770">
  <path fill="#1d3b83" d="M0,4190 C120,4150 220,4145 330,4160 C230,4175 120,4210 0,4270 Z"/>
  <path fill="#3aa6e0" d="M0,4295 C280,4190 520,4330 820,4290 C980,4268 1100,4215 1200,4165 L1200,4910 L0,4910 Z"/>
  <path fill="#1d3b83" d="M0,4315 C300,4230 560,4370 850,4320 C1000,4295 1110,4250 1200,4220 L1200,4910 L0,4910 Z"/>
</svg>
<h2 class="abs section-title contact-title">CONTACT <span>US</span></h2>
<p class="abs lead contact-lead">Lorem ipsum dolor sit amet, consectetur adipiscing elit, sed do eiusmod tempor<br>incididunt ut labore et dolore magna aliqua. Quis ipsum suspendisse ultric</p>
<div class="abs field" style="left:283px;top:4555px;width:304px;height:42px">Name:</div>
<div class="abs field" style="left:283px;top:4609px;width:304px;height:42px">Email:</div>
<div class="abs field" style="left:283px;top:4662px;width:304px;height:42px">Phone:</div>
<div class="abs field" style="left:597px;top:4555px;width:320px;height:149px">Message:</div>
<div class="abs info" style="left:254px;top:4762px"><span class="dot"><svg width="22" height="22" viewBox="0 0 24 24"><path fill="#fff" d="M12 2a7 7 0 0 0-7 7c0 5 7 13 7 13s7-8 7-13a7 7 0 0 0-7-7zm0 9.5A2.5 2.5 0 1 1 12 6a2.5 2.5 0 0 1 0 5.5z"/></svg></span><span>Lorem sipsms dolr<br>(Adrs dumy Lorem 89)</span></div>
<div class="abs info" style="left:515px;top:4762px"><span class="dot"><svg width="22" height="22" viewBox="0 0 24 24"><path fill="#fff" d="M6.6 10.8a15 15 0 0 0 6.6 6.6l2.2-2.2a1 1 0 0 1 1-.25 11.4 11.4 0 0 0 3.6.57 1 1 0 0 1 1 1V20a1 1 0 0 1-1 1A17 17 0 0 1 3 4a1 1 0 0 1 1-1h3.5a1 1 0 0 1 1 1c0 1.25.2 2.45.57 3.6a1 1 0 0 1-.25 1z"/></svg></span><span>Phone:<br>555.014.7720</span></div>
<div class="abs info" style="left:709px;top:4762px"><span class="dot"><svg width="22" height="22" viewBox="0 0 24 24"><path fill="#fff" d="M3 5h18v14H3z"/><path d="M3 6l9 7 9-7" stroke="#55b9ea" stroke-width="2" fill="none"/></svg></span><span>Email Address:<br>hello@marloweaquatics.example</span></div>

<!-- footer -->
<div class="abs social" aria-label="Social links"><i></i><i></i><i></i><i></i></div>
<div class="abs brand foot-brand"><span class="brand-mark"></span><span class="brand-name">MARLOWE<br><span style="font-size:20px">AQUATICS</span></span></div>
<p class="abs copy">Copyright© 2023 All Rights Reserved.<br>Privacy Policy &nbsp;Terms and Conditions</p>

</body>
</html>
```